Plenko - Shoe Fitting App : Foot scanning app, 3D reconstruction and Fit recommandation.

We are a startup that has developed a 3D scanning App that compares the 3d reconstructed foot to the 3D Last (mould) of a shoe to find the best match and recommend a shoe size with a graphical representation of the fit on a reconstructed foot without texturing. The challenge of this app is to have a simple and intuitive onboarding of the user with clean and crisp ui and a simple tutorial for foot scanning. 3D representation of the fit is also key. What you see is what you feel is what we would like to achieve.

Target Market(s)

Sneaker Brands and athletic shoes brands

Industry/Entity Type

Footwear

Font styles to use
Other font styles liked:
• Oswald or Droid Serif

Colors
0094D4
00A9DD
6FCCEA
C7EBF8
E9F6FB

Requirements
Must have
• Simple intuitive UI to onboard the customer to scan his bare foot (please look at attached image on how to scan the foot). You must flip your phone so that the screen is facing your foot. Start at 40cm distance form the front of your foot and turn 360% slowly to capture the foot while you feel the aptic of the iPhone. That needs to be presented with a simple animation that the user can easily understand and skip if he is a returning customer and knows how to do that. the rest of the UI is to present the result of the scanned foot for the user to use to get his fit and size. The other must have is the final result screen. Where the user will a representation of the foot (snug, loose ) of different predefined areas of the foot so he can choose the fit that he likes and not necessarily the size that we suggest. Must match website design (https://www.plenko.example)
Nice to have
• An animation of the whole process (scan-compare 3d foot with 3d shoe last(or mould) and get the 3D result of the best fit + associated size. Optionaly, an option to play with your foot and transform it (avatar like with accessories and colours)
Should not have
• Too many colours. Too much text. No gender type. No race type.

```html
<!DOCTYPE html>
<html lang="en">
<head>
<meta charset="utf-8">
<title>Plenko – Foot Scan Onboarding Screens</title>
<link rel="stylesheet" href="https://fonts.googleapis.com/css2?family=Arimo:wght@400;700&display=swap">
<style>
:root{
  --stage:#6e6e6e;
  --phone:#080808;
  --card:#111111;
  --card-line:#2e2e2e;
  --panel:#171717;
  --teal:#4ab5b5;
  --white:#ffffff;
  --muted:#d4d4d4;
  --ink:#101010;
  --mesh-light:#d9d9d9;
  --mesh-mid:#8a8a8a;
  --mesh-dark:#1c1c1c;
  --skin-light:#edc3a6;
  --skin-mid:#c98f72;
}
*{box-sizing:border-box;margin:0;padding:0}
html,body{width:1200px;height:528px;overflow:hidden}
body{background:var(--stage);font-family:"Arimo",Arial,sans-serif;color:var(--white);position:relative}
.phone{position:absolute;top:65px;width:180px;height:397px;background:var(--phone);border-radius:22px;overflow:hidden}
.status{position:absolute;top:8px;left:15px;right:15px;display:flex;justify-content:space-between;align-items:center;font-size:6px}
.brand{position:absolute;top:27px;left:0;right:0;text-align:center;font-weight:700;font-size:24px;letter-spacing:1px}
.card{position:absolute;left:15px;top:66px;width:150px;height:310px;background:var(--card);border:1px solid var(--card-line);border-radius:10px}
.intro{position:absolute;left:8px;top:8px;width:133px;height:79px;background:var(--panel);border-radius:8px;text-align:center;padding-top:10px}
.intro h2{font-size:10px;font-weight:700;line-height:11.6px}
.intro h2.caps{text-transform:uppercase}
.intro p{font-size:6.8px;line-height:9.6px;margin-top:5px;color:var(--white)}
.intro.short{height:55px;padding-top:13px}
.figure{position:absolute;border-radius:10px}
.figure.mesh{background:radial-gradient(ellipse 60% 55% at 50% 50%,var(--mesh-light) 0%,var(--mesh-mid) 45%,var(--mesh-dark) 100%)}
.figure.skin{background:radial-gradient(ellipse 60% 55% at 55% 55%,var(--skin-light) 0%,var(--skin-mid) 50%,#3a2a22 100%)}
.scan-label{position:absolute;font-size:4.6px;color:var(--teal)}
.badge-360{position:absolute;width:22px;height:22px;border-radius:50%;background:var(--white);color:var(--ink);font-size:5.5px;font-weight:700;display:flex;align-items:center;justify-content:center}
.dots{position:absolute;top:242px;left:0;right:0;display:flex;justify-content:center;gap:4px}
.dots span{width:5px;height:5px;border:1px solid var(--white);border-radius:1px}
.dots span.on{background:var(--white)}
.btn{position:absolute;left:14px;width:121px;height:17px;border-radius:9px;font-size:6.8px;font-weight:700;display:flex;align-items:center;justify-content:center;text-transform:uppercase}
.btn.primary{top:257px;background:var(--teal);color:var(--white)}
.btn.light{background:var(--white);color:var(--ink)}
.homebar{position:absolute;top:289px;left:44px;width:62px;height:2px;background:var(--white);border-radius:1px}
.eye{position:absolute;left:12px;top:223px}
.loading .intro{height:72px;padding-top:12px}
.loading .intro p{margin-top:4px}
.percent{font-size:6px;font-weight:700;color:var(--teal);margin-top:3px}
.progress{position:absolute;left:12px;right:12px;bottom:8px;height:4px;background:#2b2b2b;border-radius:2px}
.facts{position:absolute;top:89px;left:4px;right:4px;text-align:center}
.facts h3{font-size:6.6px;font-weight:700;text-transform:uppercase}
.facts p{font-size:4.7px;line-height:7.6px;margin-top:3px;color:var(--white)}
.facts p + p{margin-top:2px}
.avatar{position:absolute;left:52px;top:137px;width:48px;height:48px;border-radius:50%;background:var(--white);border:3px solid #4a4a4a;overflow:hidden}
.avatar .figure{inset:7px;border-radius:50%}
.pref{position:absolute;left:11px;width:130px;background:var(--teal);border-radius:5px;text-align:center}
.pref.ask{top:189px;height:61px;padding-top:5px}
.pref.ask h3{font-size:6.6px;font-weight:700;text-transform:uppercase}
.pref.ask p{font-size:4.6px;margin-top:3px}
.options{display:flex;justify-content:center;gap:3px;margin:4px 0 3px}
.options span{width:13px;height:13px;border-radius:50%;background:var(--white);color:var(--ink);font-size:3px;display:flex;align-items:center;justify-content:center;border:1px solid var(--white)}
.options span.sel{background:var(--teal);color:var(--white)}
.pref .note{font-size:4.6px;line-height:9.5px}
.pref.tip{top:252px;height:28px;padding:3px 4px 0;font-size:4.5px;line-height:7.7px}
.loading .btn.light{top:283px}
</style>
</head>
<body>

<section class="phone" style="left:60px">
  <div class="status"><span>9:41</span><svg width="18" height="6" viewBox="0 0 18 6"><rect x="0" y="3" width="1.2" height="3" fill="#fff"/><rect x="2" y="1.5" width="1.2" height="4.5" fill="#fff"/><path d="M5 2.5a3 3 0 0 1 3.5 0M5.8 3.6a1.6 1.6 0 0 1 1.9 0" stroke="#fff" stroke-width=".7" fill="none"/><rect x="10" y="0.5" width="7" height="4.5" rx="1" fill="none" stroke="#fff" stroke-width=".7"/><rect x="11" y="1.5" width="4" height="2.5" fill="#fff"/></svg></div>
  <div class="brand">PLENKO</div>
  <div class="card">
    <div class="intro"><h2>Make Sure You're in<br>A Well Lit Area</h2><p>Avoid strong light from only one<br>direction. This casts deep shadows<br>that reduce accuracy of the scan.</p></div>
    <div class="figure mesh" style="left:26px;top:121px;width:91px;height:89px" role="img" aria-label="Wireframe illustration of two bare feet in good lighting"></div>
    <div class="dots"><span class="on"></span><span></span><span></span></div>
    <div class="btn primary">Next</div>
    <div class="homebar"></div>
  </div>
</section>

<section class="phone" style="left:285px">
  <div class="status"><span>9:41</span><svg width="18" height="6" viewBox="0 0 18 6"><rect x="0" y="3" width="1.2" height="3" fill="#fff"/><rect x="2" y="1.5" width="1.2" height="4.5" fill="#fff"/><path d="M5 2.5a3 3 0 0 1 3.5 0M5.8 3.6a1.6 1.6 0 0 1 1.9 0" stroke="#fff" stroke-width=".7" fill="none"/><rect x="10" y="0.5" width="7" height="4.5" rx="1" fill="none" stroke="#fff" stroke-width=".7"/><rect x="11" y="1.5" width="4" height="2.5" fill="#fff"/></svg></div>
  <div class="brand">PLENKO</div>
  <div class="card">
    <div class="intro"><h2>Take Off Your Shoes<br>and Roll Up Pants</h2><p>To scan your feet, the camera<br>needs to see the unique details,<br>including your ankle.</p></div>
    <div class="figure mesh" style="left:12px;top:107px;width:128px;height:124px" role="img" aria-label="Wireframe legs with bare feet beside removed sneakers and socks"></div>
    <div class="dots"><span></span><span class="on"></span><span></span></div>
    <div class="btn primary">Next</div>
    <div class="homebar"></div>
  </div>
</section>

<section class="phone" style="left:510px">
  <div class="status"><span>9:41</span><svg width="18" height="6" viewBox="0 0 18 6"><rect x="0" y="3" width="1.2" height="3" fill="#fff"/><rect x="2" y="1.5" width="1.2" height="4.5" fill="#fff"/><path d="M5 2.5a3 3 0 0 1 3.5 0M5.8 3.6a1.6 1.6 0 0 1 1.9 0" stroke="#fff" stroke-width=".7" fill="none"/><rect x="10" y="0.5" width="7" height="4.5" rx="1" fill="none" stroke="#fff" stroke-width=".7"/><rect x="11" y="1.5" width="4" height="2.5" fill="#fff"/></svg></div>
  <div class="brand">PLENKO</div>
  <div class="card">
    <div class="intro short"><h2 class="caps">Flip the screen<br>towards your toes<br>to start scanning</h2></div>
    <div class="figure mesh" style="left:36px;top:84px;width:82px;height:116px" role="img" aria-label="Wireframe foot with a dotted 360 degree scanning path"></div>
    <span class="scan-label" style="left:113px;top:146px">40 cm</span>
    <div class="badge-360" style="left:12px;top:178px">360°</div>
    <div class="dots"><span></span><span></span><span class="on"></span></div>
    <div class="btn primary">Left Foot</div>
    <div class="homebar"></div>
  </div>
</section>

<section class="phone" style="left:735px">
  <div class="status"><span>9:41</span><svg width="18" height="6" viewBox="0 0 18 6"><rect x="0" y="3" width="1.2" height="3" fill="#fff"/><rect x="2" y="1.5" width="1.2" height="4.5" fill="#fff"/><path d="M5 2.5a3 3 0 0 1 3.5 0M5.8 3.6a1.6 1.6 0 0 1 1.9 0" stroke="#fff" stroke-width=".7" fill="none"/><rect x="10" y="0.5" width="7" height="4.5" rx="1" fill="none" stroke="#fff" stroke-width=".7"/><rect x="11" y="1.5" width="4" height="2.5" fill="#fff"/></svg></div>
  <div class="brand">PLENKO</div>
  <div class="card">
    <div class="intro short"><h2>Please check that the<br>reconstruction of your<br>foot seems correct</h2></div>
    <div class="figure skin" style="left:25px;top:111px;width:92px;height:80px" role="img" aria-label="3D reconstruction of the scanned bare foot"></div>
    <svg class="eye" width="10" height="7" viewBox="0 0 10 7"><path d="M0.5 3.5C2 1 3.5 0.5 5 0.5S8 1 9.5 3.5C8 6 6.5 6.5 5 6.5S2 6 0.5 3.5Z" fill="#4ab5b5"/><circle cx="5" cy="3.5" r="1.4" fill="#111"/></svg>
    <div class="btn light" style="top:237px">Scan Again</div>
    <div class="btn primary">My Fit</div>
    <div class="homebar"></div>
  </div>
</section>

<section class="phone loading" style="left:960px">
  <div class="status"><span>9:41</span><svg width="18" height="6" viewBox="0 0 18 6"><rect x="0" y="3" width="1.2" height="3" fill="#fff"/><rect x="2" y="1.5" width="1.2" height="4.5" fill="#fff"/><path d="M5 2.5a3 3 0 0 1 3.5 0M5.8 3.6a1.6 1.6 0 0 1 1.9 0" stroke="#fff" stroke-width=".7" fill="none"/><rect x="10" y="0.5" width="7" height="4.5" rx="1" fill="none" stroke="#fff" stroke-width=".7"/><rect x="11" y="1.5" width="4" height="2.5" fill="#fff"/></svg></div>
  <div class="brand">PLENKO</div>
  <div class="card">
    <div class="intro"><h2>Loading Your Data</h2><p>This process might take a few<br>minutes</p><div class="percent">0%</div><div class="progress"></div></div>
    <div class="facts">
      <h3>Fun facts about feet</h3>
      <p>Our feet have nearby a Quater of all bones in our<br>bodies-each one has 26 bones.</p>
      <p>Feet grow as we age - our arch may flatten,<br>causing our foot size to increase.</p>
    </div>
    <div class="avatar"><div class="figure skin" role="img" aria-label="Soles of two bare feet"></div></div>
    <div class="pref ask">
      <h3>Tell us your preference</h3>
      <p>How do you prefer the cushion?</p>
      <div class="options"><span>Soft</span><span class="sel">Medium</span><span>Hard</span></div>
      <div class="note">Select an option to go to the next personal<br>preference setting</div>
    </div>
    <div class="pref tip">Click below to see how this shoe fits. Now that you're<br>scanned, you can quickly try other shoes without<br>going through the process again.</div>
    <div class="btn light">See Results</div>
  </div>
</section>

</body>
</html>
```